Stationary Set Rebrand for Brennick

We are a Canadian Distribution and Service Company that was established in 1969. Over the past 5 decades we have expanded our business and have warehouses across Canada. We specialize in adhesive tapes, adhesives, films, safety, warehouse, shipping, janitorial and packaging supplies.

We have updated our logo design and would like a new corporate branding identity that includes a new fresh Stationary Set (Business Cards, Letterhead, Letterhead MS Word, Envelope, Presentation Folders, Email Signatures, Notepad Covers, etc.)

Target Market(s)

Industrial Business Sector

Font styles to use
Sans Serif

Colors
0054AA
0677BA
7BADD7
CADEEF
E8F1F8
0094D4
00A9DD
6FCCEA
C7EBF8
E9F6FB
00AB8E
00BBA5
67D7C9
C6EFE9
E9F9F6
EB3D1F
EC4F4E
F09395
F8D3D4
FCEDEE

Requirements
Should not have
• Colors not too light, darker colours preferred

```html
<!DOCTYPE html>
<html lang="en">
<head>
<meta charset="utf-8">
<title>Brennick Business Card</title>
<link href="https://fonts.googleapis.com/css2?family=Nunito:wght@400;600;800&display=swap" rel="stylesheet">
<style>
  :root {
    --stage: #e6e6e6;
    --card: #1b1b1c;
    --red: #eb3d1f;
    --red-soft: #d9312f;
    --white: #f4f4f4;
    --grey-light: #4a4a4b;
    --grey-dark: #161617;
  }
  * { margin: 0; padding: 0; box-sizing: border-box; }
  html, body {
    width: 1200px;
    height: 1083px;
    overflow: hidden;
    background: var(--stage);
    font-family: "Nunito", Arial, sans-serif;
  }
  .sheet {
    position: relative;
    width: 1200px;
    height: 1083px;
  }
  .card {
    position: absolute;
    left: 180px;
    width: 840px;
    height: 480px;
    background: var(--card);
    overflow: hidden;
    box-shadow: 0 10px 30px rgba(0,0,0,0.18);
  }
  .card--front { top: 41px; }
  .card--back { top: 561px; }

  .brand {
    position: absolute;
    left: 64px;
    top: 54px;
    display: flex;
    align-items: center;
    gap: 14px;
  }
  .brand__name {
    font-weight: 800;
    font-size: 66px;
    line-height: 1;
    color: var(--white);
    letter-spacing: -0.5px;
  }
  .brand__mark {
    width: 16px;
    height: 16px;
    background: var(--red);
    margin-top: 30px;
  }

  .person {
    position: absolute;
    left: 520px;
    top: 150px;
    padding-left: 22px;
    border-left: 2px solid var(--red);
  }
  .person__name {
    font-size: 30px;
    font-weight: 600;
    color: var(--red);
    letter-spacing: 1px;
    text-transform: uppercase;
    line-height: 1.15;
  }
  .person__role {
    font-size: 21px;
    color: var(--white);
    margin-top: 4px;
  }

  .contact {
    position: absolute;
    left: 64px;
    top: 230px;
    color: var(--white);
    font-size: 21px;
    line-height: 1.35;
  }
  .contact__address { margin-bottom: 14px; padding-left: 28px; }
  .contact__line {
    display: flex;
    align-items: center;
    gap: 10px;
  }
  .contact__icon {
    width: 18px;
    height: 18px;
    flex: none;
  }

  .front-feature {
    position: absolute;
    right: 0;
    bottom: 0;
    width: 420px;
    height: 190px;
    background: var(--red-soft);
    border-top-left-radius: 140px;
  }

  .back-pattern {
    position: absolute;
    inset: 0;
    background: linear-gradient(120deg, var(--grey-light) 0%, #2a2a2b 45%, var(--grey-dark) 75%);
  }
</style>
</head>
<body>
<main class="sheet">

  <section class="card card--front" aria-label="Business card front">
    <div class="brand">
      <span class="brand__name">Brennick</span>
      <span class="brand__mark"></span>
    </div>

    <div class="person">
      <p class="person__name">Daniel Marsh</p>
      <p class="person__role">Development Manager Officer</p>
    </div>

    <div class="contact">
      <p class="contact__address">412 Harbour Road<br>Unit 18, Oakville, ON L6K 2B4</p>
      <p class="contact__line">
        <svg class="contact__icon" viewBox="0 0 24 24" aria-hidden="true"><path fill="#eb3d1f" d="M6.6 10.8a15.1 15.1 0 0 0 6.6 6.6l2.2-2.2c.3-.3.7-.4 1-.2 1.1.4 2.3.6 3.6.6.6 0 1 .4 1 1V20c0 .6-.4 1-1 1A17 17 0 0 1 3 4c0-.6.4-1 1-1h3.5c.6 0 1 .4 1 1 0 1.3.2 2.5.6 3.6.1.3 0 .7-.2 1z"/></svg>
        905-214-3370
      </p>
      <p class="contact__line">
        <svg class="contact__icon" viewBox="0 0 24 24" aria-hidden="true"><rect x="2" y="5" width="20" height="14" rx="1.5" fill="#eb3d1f"/><path d="M3 6l9 7 9-7" fill="none" stroke="#1b1b1c" stroke-width="1.6"/></svg>
        daniel.marsh@brennicksupply.ca
      </p>
      <p class="contact__line">
        <svg class="contact__icon" viewBox="0 0 24 24" aria-hidden="true"><g fill="none" stroke="#eb3d1f" stroke-width="1.6"><circle cx="12" cy="12" r="9"/><ellipse cx="12" cy="12" rx="4" ry="9"/><path d="M3 12h18M5 7h14M5 17h14"/></g></svg>
        brennicksupply.ca
      </p>
    </div>

    <div class="front-feature" role="img" aria-label="Large red brand emblem decoration"></div>
  </section>

  <section class="card card--back" aria-label="Business card back">
    <div class="back-pattern" role="img" aria-label="Repeating glossy brand emblem pattern fading from grey to black"></div>
  </section>

</main>
</body>
</html>
```